Wine Bottle Label for Corra Winslow California Wine

This will be a wine bottle label. The wine is produced from grapes from our family farm. Images at bottom are some of same ones in high resolution

Corra Winslow
Reserve Pinot Noir
Clarksburg 2023
Estate Grown (in cursive)

We would like to have a view from above, looking down from the levee there is a slough (wing of a river) running behind it, it looks down over vineyards, a big wood barn, a giant Oak Tree beyond the barn. There are beautiful sunsets there in the distance. Many birds fly over the vineyards including small black birds (as shown in one photo). Please use what you can from these suggestions to make a label. We will need a small image for back label and wording on it.

Other font styles liked:
• Wine bottle fonts

Requirements
Must have
• Wording mentioned . An Oak Tree with images of the vines and a sunset
Nice to have
• Flock of black birds flying in the sky

```html
<!DOCTYPE html>
<html lang="en">
<head>
<meta charset="utf-8">
<title>Corra Winslow Reserve Pinot Noir – Front Label</title>
<link href="https://fonts.googleapis.com/css2?family=Italiana&family=Montserrat:wght@400;600&family=Pinyon+Script&display=swap" rel="stylesheet">
<style>
  :root {
    --backdrop: #2a2a2c;
    --label-paper: #f6f4f4;
    --ink: #151515;
    --ink-soft: #3c3c3c;
    --sketch-tone: #dcdcdc;
    --sketch-tone-deep: #c4c4c4;
    --wine-red: #8e0a0c;
    --wine-red-deep: #5e0306;
    --gold: #b8963e;
    --band-text: #e9dede;
  }
  * { margin: 0; padding: 0; box-sizing: border-box; }
  html, body {
    width: 1200px;
    height: 800px;
    overflow: hidden;
    background: var(--backdrop);
  }
  .canvas {
    position: relative;
    width: 1200px;
    height: 800px;
  }
  .label {
    position: absolute;
    left: 120px;
    top: 60px;
    width: 960px;
    height: 680px;
    background: var(--label-paper);
    overflow: hidden;
  }
  .artwork {
    position: absolute;
    border-radius: 8px;
  }
  .artwork--vineyard {
    left: 330px;
    top: 40px;
    width: 300px;
    height: 220px;
    background: linear-gradient(180deg, #ececec 0%, var(--sketch-tone) 55%, var(--sketch-tone-deep) 100%);
  }
  .artwork--grapes-left {
    left: 30px;
    top: 90px;
    width: 140px;
    height: 200px;
    background: linear-gradient(170deg, #eeeeee 0%, var(--sketch-tone) 100%);
  }
  .artwork--grapes-right {
    left: 790px;
    top: 20px;
    width: 140px;
    height: 250px;
    background: linear-gradient(190deg, #eeeeee 0%, var(--sketch-tone) 100%);
  }
  .wine-name {
    position: absolute;
    left: 0;
    right: 0;
    top: 302px;
    text-align: center;
    font-family: "Italiana", serif;
    font-size: 112px;
    font-weight: 400;
    line-height: 1;
    color: var(--ink);
    letter-spacing: 1px;
  }
  .wine-variety {
    position: absolute;
    left: 0;
    right: 0;
    top: 438px;
    text-align: center;
    font-family: "Montserrat", sans-serif;
    font-size: 30px;
    font-weight: 400;
    color: var(--ink-soft);
    letter-spacing: 0.5px;
  }
  .origin-band {
    position: absolute;
    left: 0;
    bottom: 0;
    width: 960px;
    height: 180px;
  }
  .origin-band svg { display: block; }
  .appellation {
    position: absolute;
    left: 90px;
    bottom: 52px;
    font-family: "Montserrat", sans-serif;
    font-size: 30px;
    font-weight: 600;
    letter-spacing: 2px;
    color: var(--band-text);
  }
  .estate-note {
    position: absolute;
    right: 90px;
    bottom: 62px;
    font-family: "Pinyon Script", cursive;
    font-size: 44px;
    color: #ffffff;
  }
</style>
</head>
<body>
<main class="canvas">
  <section class="label">
    <div class="artwork artwork--grapes-left" role="img" aria-label="Pencil-sketch grape cluster with vine leaves"></div>
    <div class="artwork artwork--vineyard" role="img" aria-label="Pencil-sketch of a farmhouse with cypress trees above rows of vineyard"></div>
    <div class="artwork artwork--grapes-right" role="img" aria-label="Pencil-sketch grape cluster hanging from a vine"></div>

    <h1 class="wine-name">Corra Winslow</h1>
    <p class="wine-variety">Reserve Pinot Noir</p>

    <div class="origin-band">
      <svg width="960" height="180" viewBox="0 0 960 180" aria-hidden="true">
        <defs>
          <linearGradient id="bandRed" x1="0" y1="0" x2="1" y2="0">
            <stop offset="0" stop-color="var(--wine-red-deep)"/>
            <stop offset="0.5" stop-color="var(--wine-red)"/>
            <stop offset="1" stop-color="var(--wine-red)"/>
          </linearGradient>
        </defs>
        <path d="M0 40 Q480 -10 960 30 L960 180 L0 180 Z" fill="url(#bandRed)"/>
        <path d="M0 40 Q480 -10 960 30" fill="none" stroke="var(--gold)" stroke-width="5"/>
      </svg>
      <span class="appellation">CLARKSBURG 2023</span>
      <span class="estate-note">Estate Grown</span>
    </div>
  </section>
</main>
</body>
</html>
```